CV Template

We need a graphic design to our new CV templates for our consultants. We are a small young Danish upcoming IT-business company making software solutions for our customers etc. You can visit our new website here: dev.sol-brovaerk.com, then you can see our web design, colors etc. I have attached a file for your inspiration :-) In the presentation I would like to have a picture of the employee, some text who descripe the profile/consultant and then I imagine that there is a table where we can write the employee's skills etc.

I would like the design to be "fresh & catchy" :-)

Looking forward to hear from you.

Best regards,
Hanne

```html
<!DOCTYPE html>
<html lang="en">
<head>
<meta charset="utf-8">
<title>CV Template – Alexander Test</title>
<link rel="stylesheet" href="https://fonts.googleapis.com/css2?family=Open+Sans:wght@700&family=PT+Sans+Narrow:wght@700&family=Source+Sans+3:ital,wght@0,400;0,600;0,700;1,400&display=swap">
<style>
  :root {
    --orange: #f07f22;
    --orange-dark: #b85a12;
    --orange-line: #f9c79c;
    --navy: #234f6a;
    --card: #ededed;
    --ink: #1e1e1e;
    --muted: #c2c2c2;
    --photo-bg: #b6b8bb;
    --paper: #ffffff;
  }
  * { box-sizing: border-box; margin: 0; padding: 0; }
  html, body { width: 1200px; height: 900px; overflow: hidden; background: var(--paper); }
  body { position: relative; font-family: "Source Sans 3", "Myriad Pro", sans-serif; color: var(--ink); }

  .sidebar { position: absolute; left: 60px; top: 71px; width: 284px; height: 657px; background: var(--orange); color: var(--paper); text-align: center; }
  .portrait { position: absolute; left: 68px; top: 41px; width: 140px; height: 140px; border: 4px solid var(--paper); background: var(--photo-bg); }
  .profile-name { position: absolute; left: 0; width: 100%; top: 196px; font-family: "PT Sans Narrow", "Myriad Pro Condensed", sans-serif; font-weight: 700; font-size: 29px; }
  .profile-role { position: absolute; left: 0; width: 100%; top: 238px; font-style: italic; font-size: 16px; color: var(--orange-dark); }
  .sidebar-rule { position: absolute; left: 26px; top: 300px; width: 225px; height: 1px; background: var(--orange-line); }
  .profile-summary { position: absolute; left: 0; width: 100%; top: 373px; font-style: italic; font-size: 17.5px; line-height: 30.5px; }

  .contact-bar { position: absolute; left: 344px; top: 71px; width: 787px; height: 45px; background: var(--navy); color: var(--paper); font-style: italic; font-size: 12.5px; }
  .contact-item { position: absolute; top: 14px; display: flex; align-items: center; gap: 9px; }
  .contact-item svg { display: block; }
  .contact-email { left: 20px; }
  .contact-phone { left: 180px; }

  .section-title { position: absolute; width: 124px; height: 40px; background: var(--navy); color: var(--paper); font-family: "Open Sans", sans-serif; font-weight: 700; font-size: 15.5px; display: flex; align-items: center; justify-content: center; letter-spacing: 0.2px; }

  .timeline-axis { position: absolute; left: 367px; top: 211px; width: 4px; height: 508px; background: var(--navy); }
  .timeline-dot { position: absolute; left: 360px; width: 18px; height: 18px; border-radius: 50%; background: var(--navy); }
  .timeline-card { position: absolute; left: 403px; width: 222px; background: var(--card); padding: 8px 11px 0; }
  .timeline-card::before { content: ""; position: absolute; left: -9px; top: var(--notch); border-style: solid; border-width: 9px 9px 9px 0; border-color: transparent var(--card) transparent transparent; }
  .timeline-year { font-weight: 700; font-size: 17px; color: var(--navy); line-height: 20px; margin-bottom: 5px; }
  .timeline-text { font-size: 12.5px; line-height: 21.6px; }
  .timeline-present { display: flex; align-items: center; padding-top: 0; }
  .timeline-present .timeline-year { margin: 0; }

  .category-text { position: absolute; left: 706px; width: 390px; font-size: 12.5px; line-height: 21.6px; }

  .skill-list { position: absolute; left: 706px; top: 665px; list-style: none; }
  .skill-row { position: relative; height: 21.6px; display: flex; align-items: center; font-size: 12.5px; }
  .skill-name { width: 76px; }
  .skill-rating { display: flex; gap: 6px; width: 123px; }
  .skill-rating span { width: 11px; height: 11px; border-radius: 50%; border: 1px solid var(--muted); }
  .skill-rating .on { background: var(--orange); border-color: var(--orange); }
  .skill-note { font-style: italic; color: var(--muted); }

  .brand { position: absolute; left: 118px; top: 764px; font-family: "Source Sans 3", sans-serif; font-weight: 400; font-size: 22px; color: var(--navy); letter-spacing: 0.5px; }
</style>
</head>
<body>

<aside class="sidebar">
  <div class="portrait" role="img" aria-label="Portrait photo of the employee"></div>
  <h1 class="profile-name">Alexander Test</h1>
  <p class="profile-role">Position</p>
  <div class="sidebar-rule"></div>
  <p class="profile-summary">Here could be a short descrip-<br>tion of the particular employee.<br>Maybe a brief description of his<br>past, what he/she does at your<br>company, etc. I think the space<br>would be perfect for something<br>like this</p>
</aside>

<header class="contact-bar">
  <div class="contact-item contact-email">
    <svg width="18" height="13" viewBox="0 0 18 13" aria-hidden="true"><rect x="0.75" y="0.75" width="16.5" height="11.5" fill="none" stroke="#fff" stroke-width="1.5"/><path d="M1 1 L9 7.5 L17 1" fill="none" stroke="#fff" stroke-width="1.5"/></svg>
    <span>employee@email.com</span>
  </div>
  <div class="contact-item contact-phone">
    <svg width="14" height="16" viewBox="0 0 14 16" aria-hidden="true"><path d="M3 1 L5.5 4.5 L4 6.5 C5 9 6.5 10.8 8.8 12 L10.6 10.6 L13.5 13.2 L11.8 15 C6 14 1.5 8.5 1 2.6 Z" fill="#fff"/></svg>
    <span>+ 00 00 0000</span>
  </div>
</header>

<h2 class="section-title" style="left:403px;top:140px;">TIMELINE</h2>
<div class="timeline-axis"></div>
<div class="timeline-dot" style="top:202px;"></div>
<div class="timeline-dot" style="top:256px;"></div>
<div class="timeline-dot" style="top:467px;"></div>
<div class="timeline-dot" style="top:710px;"></div>

<article class="timeline-card timeline-present" style="top:192px;height:37px;--notch:10px;">
  <h3 class="timeline-year">Present</h3>
</article>
<article class="timeline-card" style="top:241px;height:130px;--notch:15px;">
  <h3 class="timeline-year">2013</h3>
  <p class="timeline-text">Finished “Project 1”. After five years of successful work, Alexander was a major contributor to the significant project development of “Project 1”.</p>
</article>
<article class="timeline-card" style="top:413px;height:147px;--notch:54px;">
  <h3 class="timeline-year">2008</h3>
  <p class="timeline-text">Project start of “Project 1”. Fulfilling clients’ wants and needs. It was a $2 million project and required to analyze, control and excute multiple tasks with business clients.</p>
</article>
<article class="timeline-card" style="top:657px;height:87px;--notch:53px;">
  <h3 class="timeline-year">1999</h3>
  <p class="timeline-text">Beginning of employment. First day at work. Some more text</p>
</article>

<h2 class="section-title" style="left:706px;top:140px;">CATEGORY</h2>
<p class="category-text" style="top:193px;">Text Text Text Text Text Text Text Text Text Text Text Text Text Text Text<br>Text Text Text Text Text Text Text Text Text Text Text Text Text Text Text<br>Text Text Text Text Text Text Text Text Text Text Text Text Text Text Text<br>Text Text Text Text Text Text Text Text Text Text Text Text Text Text Text<br>Text Text Text Text Text Text Text Text Text Text Text Text Text Text Text<br>Text Text Text Text Text Text Text Text Text Text Text Text Text Text Text</p>

<h2 class="section-title" style="left:706px;top:350px;">CATEGORY</h2>
<p class="category-text" style="top:403px;">Text Text Text Text Text Text Text Text Text Text Text Text Text Text Text<br>Text Text Text Text Text Text Text Text Text Text Text Text Text Text Text<br>Text Text Text Text Text Text Text Text Text Text Text Text Text Text Text<br>Text Text Text Text Text Text Text Text Text Text Text Text Text Text Text<br>Text Text Text Text Text Text Text Text Text Text Text Text Text Text Text<br>Text Text Text Text Text Text Text Text Text Text Text Text Text Text Text</p>

<h2 class="section-title" style="left:706px;top:611px;">SKILLS</h2>
<ul class="skill-list">
  <li class="skill-row"><span class="skill-name">Skill 1</span><span class="skill-rating"><span class="on"></span><span class="on"></span><span class="on"></span><span></span><span></span></span><span class="skill-note">Very brief description</span></li>
  <li class="skill-row"><span class="skill-name">Skill 2</span><span class="skill-rating"><span class="on"></span><span class="on"></span><span class="on"></span><span></span><span></span></span><span class="skill-note">Very brief description</span></li>
  <li class="skill-row"><span class="skill-name">Skill 3</span><span class="skill-rating"><span class="on"></span><span class="on"></span><span class="on"></span><span></span><span></span></span><span class="skill-note">Very brief description</span></li>
  <li class="skill-row"><span class="skill-name">Skill 4</span><span class="skill-rating"><span class="on"></span><span class="on"></span><span class="on"></span><span></span><span></span></span><span class="skill-note">Very brief description</span></li>
</ul>

<div class="brand">Sol Brovaerk</div>

</body>
</html>
```